Redesign This Psychology Website

We would like a slight redesign of this successful psychology (relationship counselling) website:

www.TheKelvaleClinic.com.au

We are updating the website, and we'd like a slight refresh of the design and style.

Please keep to very similar colours, and use the same logo. We're looking for around 10 page templates, however the main one is the home page.

Keep in mind, this website already converts quite well, so we want a new, fresh design in keeping with this one. Please don't bother designing something too extremely different.

thanks :)

Target Market(s)

couples who are looking for relationship counselling. Men and women, 25 - 70, across Australia

Industry/Entity Type

Psychology

Number of Pages Required

5+ page

Font styles to use
Sans Serif

Colors
87cfc6
b7a5cd
ec1f27
ffffff
cee9f5

Requirements
Must have
• a similar look to the current design, just looking for a slight refresh.
• Search bar
• Areas for lots of photos
• same logo
• lots of content areas
Nice to have
• great content areas, where we can display a lot of content and our areas.
Should not have
• no colors like orange, etc.
• should not have a totally different feel.

```html
<!DOCTYPE html>
<html lang="en">
<head>
<meta charset="utf-8">
<title>The Kelvale Clinic – Relationship Counselling</title>
<link href="https://fonts.googleapis.com/css2?family=Open+Sans:wght@400;600;700&family=Bree+Serif&display=swap" rel="stylesheet">
<style>
:root{
  --teal:#87cfc6;
  --lilac:#b7a5cd;
  --red:#ec1f27;
  --white:#ffffff;
  --sky:#cee9f5;
  --lime:#a9cd3a;
  --green:#58b947;
  --topbar:#2b8fb3;
  --brand:#1d9aa3;
  --ink:#333;
  --muted:#555;
  --dark:#202020;
  --yellow:#f6e21a;
}
*{box-sizing:border-box;margin:0;padding:0}
html,body{width:1200px;height:3622px;overflow:hidden}
body{font-family:"Open Sans",Arial,sans-serif;color:var(--ink);background:var(--white);position:relative}
.serif{font-family:"Bree Serif",Georgia,serif}

.topbar{height:29px;background:var(--topbar);color:#fff;font-size:12px;display:flex;justify-content:flex-end;align-items:center;gap:26px;padding-right:56px}
.topbar span{display:flex;align-items:center;gap:6px}

.header{height:91px;display:flex;align-items:center;justify-content:space-between;padding:0 68px}
.logo{display:flex;align-items:center;gap:10px}
.logo .dot{width:44px;height:44px;border-radius:50%;background:var(--brand)}
.logo .name{font-size:26px;font-weight:600;color:var(--brand);line-height:1}
.logo .tag{font-size:12px;color:var(--brand);margin-top:4px}
.nav{display:flex;font-size:13px;font-weight:400;text-transform:uppercase;color:#333}
.nav a{color:inherit;text-decoration:none;padding:32px 18px;border-top:4px solid transparent}
.nav a.active{border-top-color:var(--green)}

.hero{position:relative;height:616px;background:linear-gradient(180deg,#4a8fd6 0%,#9ec6ee 40%,#c5cf8a 62%,#7f9b3a 80%,#5a7a24 100%)}
.hero-copy{position:absolute;left:68px;top:168px;width:420px;color:#fff}
.hero-copy h1{font-size:46px;font-weight:700;color:var(--red);margin-bottom:18px}
.hero-copy p{font-size:16px;line-height:1.45;margin-bottom:24px;color:#1d2a3a}
.btn{display:inline-block;font-weight:700;font-size:15px;padding:12px 26px;color:#fff;background:var(--brand);text-decoration:none}

.services{position:absolute;left:68px;top:700px;width:1064px;height:382px;display:flex}
.service{flex:1;text-align:center;padding:30px 22px 0;color:#fff;position:relative}
.service h2{font-size:19px;font-weight:700;text-transform:uppercase;line-height:1.35;margin-bottom:22px}
.service p{font-size:15px;line-height:1.5;height:150px}
.service em{display:block;font-size:14px;line-height:1.4;margin:30px 0 14px}
.service .more{display:inline-block;width:110px;padding:8px 0;border:2px solid #fff;background:#fff;color:#555;font-weight:700;font-size:15px}
.s1{background:var(--teal)}.s2{background:var(--lilac)}.s3{background:var(--sky);color:#333}.s4{background:var(--lime)}
.s3 .more{border-color:#777}

.main{position:absolute;top:1135px;left:68px;width:1064px;display:flex;justify-content:space-between}
.content{width:752px;font-size:13.5px;line-height:1.55;color:var(--muted)}
.content h2{font-size:28px;color:#333;font-weight:400;margin:0 0 22px}
.content p{margin-bottom:20px}
.issues{display:grid;grid-template-columns:1fr 1fr 1fr;column-gap:20px;margin-top:10px}
.issues ul{list-style:none}
.issues li{padding-left:16px;position:relative;margin-bottom:6px}
.issues li::before{content:"›";position:absolute;left:0;color:var(--green);font-weight:700}

.aside{width:253px}
.ad{position:relative;height:200px;margin-bottom:16px;background:linear-gradient(90deg,#fbe3e0,#f3c9c0)}
.ad h3{position:absolute;left:8px;top:8px;width:125px;color:var(--red);font-size:21px;font-style:italic;line-height:1.15}
.ad .bar{position:absolute;left:0;right:0;bottom:0;height:30px;background:var(--red);color:#fff;font-size:11px;padding:2px 8px;line-height:1.25}
.ad2{background:linear-gradient(90deg,#e6f0f7,#cfe2ee)}
.ad2 h3{left:auto;right:8px;top:74px;color:#1f3d5a;font-size:20px;width:130px}
.ad2 .bar{background:var(--topbar);height:24px;padding-top:4px}
.rebates h3{color:var(--red);font-size:17px;font-weight:700;margin:18px 0 10px}
.badges{display:grid;grid-template-columns:repeat(4,1fr);gap:6px;margin-bottom:8px}
.badges span{height:34px;border-radius:4px;background:#d9e8cc}
.badges span:nth-child(2n){background:#cde0ef}
.badges span:first-child{grid-column:span 2;background:#8fc03a}
.rebates .pm{text-align:center;color:var(--topbar);font-size:12px;margin-bottom:4px}
.rebates p{font-size:15px;color:#777;line-height:1.3}
.rebates p b{color:var(--red)}
.rebates .link{margin-top:8px;background:var(--topbar);color:#fff;font-size:13px;padding:4px 8px}

.green{position:absolute;top:2000px;left:0;width:1200px;height:487px;background:var(--green);color:#fff}
.green h2{font-size:26px;font-weight:400;position:absolute;top:28px}
.video{position:absolute;left:68px;top:82px;width:505px;height:288px;border:4px solid #fff;background:linear-gradient(90deg,#b9d9ee,#e8c7a8)}
.video .ctrl{position:absolute;left:0;right:0;bottom:0;height:24px;background:rgba(0,0,0,.75)}
.video .cap{position:absolute;left:20px;bottom:30px;background:#fff;color:#333;font-size:12px;padding:2px 8px}
.green .intro{position:absolute;left:68px;top:388px;width:505px;font-size:13.5px;line-height:1.5}
.blog{position:absolute;left:618px;width:514px;height:116px}
.blog .thumb{position:absolute;left:0;top:0;width:170px;height:102px;border:3px solid #fff;background:linear-gradient(120deg,#cfcfcf,#8e8e8e)}
.blog h3{position:absolute;left:190px;top:0;font-size:16px;font-weight:700}
.blog .meta{position:absolute;left:190px;top:26px;font-size:12px;display:flex;align-items:center;gap:4px}
.blog .meta svg{flex:none}
.blog p{position:absolute;left:190px;top:46px;width:310px;font-size:13px;line-height:1.45}
.blog .date{position:absolute;right:0;top:12px;background:var(--yellow);color:#333;font-weight:700;font-size:14px;padding:7px 10px}

.finder{position:absolute;top:2487px;left:0;width:1200px;height:518px}
.finder h2{text-align:center;font-size:46px;color:#333;font-weight:400;margin-top:78px}
.form{position:absolute;left:190px;top:190px;width:690px;font-size:15px}
.row{display:flex;align-items:center;height:40px;margin-bottom:22px}
.row label{width:160px;text-align:right;padding-right:14px}
.field{flex:1;height:38px;border:1px solid #ccc;background:#fff;font-size:13px;color:#999;padding:10px}
.or{margin-left:172px;display:flex;align-items:center;gap:14px;color:#555;margin-bottom:22px;font-size:18px}
.or i{flex:1;height:1px;background:#aaa}
.submit{margin-left:172px;height:54px;background:var(--red);color:#fff;font-weight:700;font-size:22px;display:flex;align-items:center;justify-content:center}

.register{position:absolute;top:3005px;left:0;width:1200px;height:290px;background:var(--lilac);text-align:center;color:#fff}
.register h2{font-size:27px;font-weight:400;letter-spacing:1px;margin-top:66px}
.register p{font-size:15px;width:560px;margin:18px auto 24px;line-height:1.5}
.reg-btns{display:flex;justify-content:center;gap:26px}
.reg-btns span{width:228px;height:44px;line-height:44px;font-size:13px;font-weight:700}
.signup{background:var(--brand)}
.login{background:#fff;color:#555}

.footer{position:absolute;top:3295px;left:0;width:1200px;height:327px;background:var(--dark);color:#ccc;text-align:center}
.footer .logo{justify-content:center;margin-top:56px}
.footer .logo .dot{background:#8a8a8a}
.footer .logo .name,.footer .logo .tag{color:#ddd}
.fnav{display:flex;justify-content:center;gap:40px;font-size:12px;margin-top:40px;color:#fff}
.copy{font-size:13px;margin-top:22px}
.social{display:flex;justify-content:center;gap:24px;margin-top:30px}
.social span{width:30px;height:30px;border-radius:50%;background:#3a3a3a}
</style>
</head>
<body>

<div class="topbar">
  <span><svg width="12" height="12" viewBox="0 0 12 12"><path d="M6 1a3.5 3.5 0 0 0-3.5 3.5C2.5 7.5 6 11 6 11s3.5-3.5 3.5-6.5A3.5 3.5 0 0 0 6 1z" fill="#b6e06a"/></svg>Level 12, 88 Wattle Street Sydney 2000 Australia</span>
  <span><svg width="12" height="12" viewBox="0 0 12 12"><circle cx="6" cy="6" r="5" fill="none" stroke="#b6e06a" stroke-width="1.5"/><path d="M6 3v3l2 1.5" stroke="#b6e06a" stroke-width="1.5" fill="none"/></svg>Mon - Satday: 9.00 am to 6.00 pm.</span>
</div>

<header class="header">
  <div class="logo">
    <span class="dot"></span>
    <div><div class="name">The Kelvale Clinic</div><div class="tag">helping you create loving relationships</div></div>
  </div>
  <nav class="nav">
    <a class="active">Home</a><a>About</a><a>Resources</a><a>Blog</a><a>Shop</a><a>Cart</a><a>Search</a>
  </nav>
</header>

<section class="hero" role="img" aria-label="Family with a child on the father's shoulders in a sunny summer meadow">
  <div class="hero-copy">
    <h1>The Kelvale Clinic</h1>
    <p>Lorem ipsum dolor sit amet conse ctetur adipiscing elit, sed do eiusmod tempor incididunt.Lorem ipsum dolor sit amet conse ctetur adipiscing elit, sed do eiusmod tempor incididun</p>
    <a class="btn">Read More</a>
  </div>
</section>

<section class="services">
  <div class="service s1"><h2>Relationship<br>Counselling</h2><p>Communication, Recovering from an affair, Loss of intimacy &amp; love, Power battles, Feeling like friends, not lovers</p><em>Take our Relationship Quiz<br>Pre-marriage</em><span class="more">More</span></div>
  <div class="service s2"><h2>Sex Therapy<br>Counselling</h2><p>Do you need help with:<br>Low libido , Erectile difficulties, Premature ejaculation, Differing libidos, Porn addiction, Keeping sex exciting</p><em>Take our<br>Sex Quiz</em><span class="more">More</span></div>
  <div class="service s3"><h2>Anger Management<br>Counselling</h2><p>Do you need help with:<br>Managing angry outbursts, expressing your anger in healthy ways</p><em>Take our<br>Anger Test</em><span class="more">More</span></div>
  <div class="service s4"><h2>Narcissism<br>Counselling</h2><p>Do you need help with:<br>Managing narcissistic, superior, entitled, arrogant and lack of empathy tendencies in you or your partner</p><em>Check your Narcissism<br>Profile</em><span class="more">More</span></div>
</section>

<section class="main">
  <div class="content">
    <h2 class="serif">We Specialise in Relationship &amp; Marriage Counselling</h2>
    <p>At the Kelvale Clinic, we are a group of PSYCHOLOGISTS, Australia wide who are passionate about relationships and helping you with yours.</p>
    <p>Our vision is to provide the most highly regarded and comprehensive marriage counselling and relationship counselling, and sex therapy in Australia, at reasonable and affordable rates.</p>
    <p>When we are experiencing relationship and marriage problems, there can be a lot of pain and confusion, and it can often be difficult to cope with the other areas of our lives when we are struggling with problems with our partner.</p>
    <p>We are not taught about relationships and how to have a good one in our schools, so most of us are doing the best we know how, but lack the knowledge on how to create a better relationship.</p>
    <h2 class="serif" style="margin-top:30px">Our Kelvale Relationship Psychologists</h2>
    <p>Our team of 75 hand chosen Registered Psychologists in 81 locations Australia wide, are individually selected for their knowledge, experience, compassion, and unbiased approach to marriage counselling and sexual therapy.</p>
    <p>In addition all our Psychologists take part in our Initial Relationship Counselling Methodologies Training and yearly In-house conferences, ensuring you are in safe and experienced hands.</p>
    <p>As we are Psychologists, you may be eligible for Careway &amp; Private Health Insurance Rebates.<br>We are highly experienced and can help you with all kinds of relationship difficulties.</p>
    <p style="margin-bottom:8px">Here are some of the common ones:</p>
    <div class="issues">
      <ul><li>Affairs</li><li>Controlling behaviour</li><li>Verbal abuse</li><li>Imbalance of power</li><li>Lack of intimacy</li><li>Poor communication</li><li>Loss of love</li></ul>
      <ul><li>Relationship neglect</li><li>Sexual problems</li><li>Problems from childhood</li><li>Problems with parenting your children</li><li>Step children and in-laws</li><li>All forms of family proble</li></ul>
      <ul><li>Anger management problems</li><li>Porn addiction problems</li><li>Pre-marriage programs</li><li>Narcissism problems</li></ul>
    </div>
  </div>
  <aside class="aside">
    <div class="ad" role="img" aria-label="Portrait of a worried woman resting her chin on her hand">
      <h3>Is Anxiety, Depression or Stress bothering YOU?</h3>
      <div class="bar">Click here for <b>help</b> from Kelvale Anxiety &amp; Depression Psychologists</div>
    </div>
    <div class="ad ad2" role="img" aria-label="Doctor with stethoscope standing with arms crossed">
      <h3>Information for referring GPs &amp; health professionals</h3>
      <div class="bar">Click here for more details.</div>
    </div>
    <div class="rebates">
      <h3>Rebates Available</h3>
      <div class="badges"><span></span><span></span><span></span><span></span><span></span><span></span><span></span><span></span><span></span><span></span></div>
      <div class="pm">plus many more</div>
      <p>You may be able to receive rebates of up to <b>75% of your session costs</b> from Careway or Private Health Insurers.</p>
      <div class="link">Click here for more details.</div>
    </div>
  </aside>
</section>

<section class="green">
  <h2 class="serif" style="left:68px">What To Expect From Counselling</h2>
  <h2 class="serif" style="left:618px">Blogs</h2>
  <div class="video" role="img" aria-label="Video still of a counsellor speaking beside a happy couple">
    <div class="cap">Anna Moreton</div>
    <div class="ctrl"></div>
  </div>
  <p class="intro">Read more about our approach to counselling in our relationship counselling sessions, and frequently asked questions about the relationship and marriage counselling process.</p>

  <div class="blog" style="top:86px">
    <div class="thumb" role="img" aria-label="Couple sitting apart looking unhappy"></div>
    <h3>why am I with a narcissist</h3>
    <div class="meta"><svg width="11" height="11" viewBox="0 0 12 12"><circle cx="6" cy="6" r="5" fill="none" stroke="#fff" stroke-width="1.4"/><path d="M6 3v3l2 1.5" stroke="#fff" stroke-width="1.4" fill="none"/></svg>6.00 PM - 8.30 PM &nbsp;<svg width="10" height="11" viewBox="0 0 12 12"><path d="M6 1a3.5 3.5 0 0 0-3.5 3.5C2.5 7.5 6 11 6 11s3.5-3.5 3.5-6.5A3.5 3.5 0 0 0 6 1z" fill="#fff"/></svg>14 Harbour Lane</div>
    <p>Drive social change by connecting CN members with businesses and organizations that create social impact.</p>
    <span class="date">3rd Jul</span>
  </div>
  <div class="blog" style="top:224px">
    <div class="thumb" role="img" aria-label="Couple arguing in a kitchen"></div>
    <h3>Are You Living Steamroller?</h3>
    <div class="meta"><svg width="11" height="11" viewBox="0 0 12 12"><circle cx="6" cy="6" r="5" fill="none" stroke="#fff" stroke-width="1.4"/><path d="M6 3v3l2 1.5" stroke="#fff" stroke-width="1.4" fill="none"/></svg>6.00 PM - 8.30 PM &nbsp;<svg width="10" height="11" viewBox="0 0 12 12"><path d="M6 1a3.5 3.5 0 0 0-3.5 3.5C2.5 7.5 6 11 6 11s3.5-3.5 3.5-6.5A3.5 3.5 0 0 0 6 1z" fill="#fff"/></svg>14 Harbour Lane</div>
    <p>Drive social change by connecting CN members with businesses and organizations that create social impact.</p>
    <span class="date">6th Jul</span>
  </div>
  <div class="blog" style="top:362px">
    <div class="thumb" role="img" aria-label="Close-up of a hand raised in a stop gesture"></div>
    <h3>Are You Like in a Relationship?</h3>
    <div class="meta"><svg width="11" height="11" viewBox="0 0 12 12"><circle cx="6" cy="6" r="5" fill="none" stroke="#fff" stroke-width="1.4"/><path d="M6 3v3l2 1.5" stroke="#fff" stroke-width="1.4" fill="none"/></svg>6.00 PM - 8.30 PM &nbsp;<svg width="10" height="11" viewBox="0 0 12 12"><path d="M6 1a3.5 3.5 0 0 0-3.5 3.5C2.5 7.5 6 11 6 11s3.5-3.5 3.5-6.5A3.5 3.5 0 0 0 6 1z" fill="#fff"/></svg>14 Harbour Lane</div>
    <p>Drive social change by connecting CN members with businesses and organizations that create social impact.</p>
    <span class="date">28 Aug</span>
  </div>
</section>

<section class="finder">
  <h2 class="serif">Find Our Psychologist Near You</h2>
  <div class="form">
    <div class="row"><label>Type of Counselling:</label><div class="field">Selected</div></div>
    <div class="row"><label>Location:</label><div class="field"></div></div>
    <div class="or"><i></i>OR<i></i></div>
    <div class="row"><label>Postcode:</label><div class="field"></div></div>
    <div class="submit">Submit</div>
  </div>
</section>

<section class="register">
  <h2 class="serif">REGISTER TO RECEIVE UPDATES</h2>
  <p>We are continuously making improvements and innovations in products that can help you. Stay current with our updates</p>
  <div class="reg-btns"><span class="signup">🔒 SIGN UP FREE</span><span class="login">LOG IN</span></div>
</section>

<footer class="footer">
  <div class="logo">
    <span class="dot"></span>
    <div style="text-align:left"><div class="name">The Kelvale Clinic</div><div class="tag">helping you create loving relationships</div></div>
  </div>
  <div class="fnav"><span>HOME</span><span>ABOUT</span><span>RESOURCES</span><span>BLOG</span><span>SHOP CART</span></div>
  <div class="copy">Copyright © 2016.TheKelvaleClinic. All rights reserved</div>
  <div class="social"><span></span><span></span><span></span><span></span></div>
</footer>

</body>
</html>
```